WEBSITE REDESIGN FOR HAMMOCK MANUFACTURING COMPANY

VERITH HAMMOCKS - Verith Hammocks have been a specialist in hammock manufacturing business for over 20 years. FYI, the current website is WWW.SWAYNEST-EXAMPLE.COM.CN. We also have had a new logo designed . I have attached our new logo and old designs. You can use the old logo or new logo , so you can get a feel which one looks better with your design.

Target Market(s)

EUROPE AND NORTH AMERICA

Industry/Entity Type

Home And Garden

Font styles to use
Serif
Decorative
Script

Colors

Designer to choose colors to be used in the design.

Requirements
Must have
• Mobile friendly.
• Wildly creative and different. A website that we would expect to see 5 years from now.
• Pictures of hammocks and or people on hammock. Palm tree landscapes.
Nice to have
• Anything you feel would sell the garden hammock relaxation experience.

```html
<!DOCTYPE html>
<html lang="en">
<head>
<meta charset="utf-8">
<title>Verith Hammocks</title>
<link href="https://fonts.googleapis.com/css2?family=Roboto:wght@300;400;500&display=swap" rel="stylesheet">
<style>
:root{
  --navy:#231c78;
  --yellow:#f8c70c;
  --hero-yellow:rgba(248,206,0,.86);
  --light:#f1f1f1;
  --white:#ffffff;
  --ink:#111111;
  --grey:#555555;
  --line:#d8d8d8;
}
*{margin:0;padding:0;box-sizing:border-box}
html,body{width:1200px;height:2432px;overflow:hidden}
body{font-family:'Roboto',sans-serif;background:var(--white);position:relative;color:var(--ink)}
.abs{position:absolute}
.site-header{left:0;top:0;width:1200px;height:96px;background:var(--white)}
.brand{left:182px;top:26px;display:flex;align-items:center;gap:8px;color:var(--navy);font-weight:500;font-size:22px;letter-spacing:.5px}
.brand .dot{width:14px;height:14px;border-radius:50%;background:var(--yellow)}
.header-tools{left:746px;top:0;height:96px;display:flex}
.tool{width:68px;height:96px;border-left:1px solid var(--line);display:flex;align-items:center;justify-content:center;font-size:11px;font-weight:500}
.tool.currency{width:87px}
.tool:last-child{border-right:none}
.main-nav{left:0;top:96px;width:1200px;height:111px;background:var(--navy);display:flex;justify-content:center;align-items:center;gap:0}
.main-nav a{color:var(--white);text-decoration:none;font-size:17px;font-weight:500;margin:0 19px}
.hero{left:0;top:207px;width:1200px;height:566px;background:linear-gradient(180deg,#8fc0ea 0%,#b9d8ef 30%,#3fa7c0 45%,#77c4cc 55%,#d8cfbc 72%,#bfb29a 100%)}
.hero-panel{left:270px;top:350px;width:692px;height:233px;background:var(--hero-yellow);text-align:center}
.hero-panel h1{font-weight:400;font-size:28px;line-height:39px;margin-top:44px;color:var(--ink)}
.btn{background:var(--navy);color:var(--white);font-size:18px;display:flex;align-items:center;justify-content:center}
.hero-btn{left:271px;top:142px;width:158px;height:47px}
.arrow{top:98px}
.products{left:0;top:773px;width:1200px;height:509px;background:var(--light)}
.section-title{width:1200px;left:0;text-align:center;font-size:28px;font-weight:400}
.product-card{color:var(--white);text-align:center;display:flex;flex-direction:column;align-items:center;justify-content:center}
.product-card .name{font-size:26px;font-weight:400}
.product-card .cta{font-size:14px;margin-top:2px}
.featured-img{width:197px;height:201px}
.item{width:197px;text-align:center}
.item .by{font-size:12px;color:var(--grey)}
.item .title{font-size:18px;color:var(--navy);margin-top:10px}
.item .price{font-size:20px;color:var(--navy);margin-top:4px}
.newsletter{left:0;top:1780px;width:1200px;height:283px;background:var(--yellow)}
.email{left:311px;top:146px;width:419px;height:52px;background:var(--white);font-size:16px;color:#444;padding-left:19px;display:flex;align-items:center}
.sub-btn{left:741px;top:146px;width:160px;height:52px}
.site-footer{left:0;top:2063px;width:1200px;height:369px;background:var(--navy);color:var(--white)}
.col h3{font-size:19px;font-weight:400;margin-bottom:18px}
.col a{display:block;color:var(--white);text-decoration:none;font-size:15px;margin-bottom:12px}
.social{display:flex;gap:9px}
.social span{width:33px;height:33px;border-radius:50%;background:var(--white)}
.divider{left:182px;top:260px;width:836px;height:1px;background:#4a449a}
.cards{left:490px;top:283px;display:flex;gap:13px}
.cards span{width:32px;height:19px;background:var(--white);border-radius:2px}
.copyright{left:0;top:325px;width:1200px;text-align:center;font-size:12px;color:#c9c6ea}
</style>
</head>
<body>
<header class="site-header abs">
  <div class="brand abs"><span class="dot"></span>VERITH HAMMOCKS</div>
  <div class="header-tools abs">
    <div class="tool currency">USD ▾</div>
    <div class="tool"><svg width="18" height="18" viewBox="0 0 18 18" fill="none" stroke="#111" stroke-width="1.6"><circle cx="7.5" cy="7.5" r="5.5"/><path d="M12 12l5 5"/></svg></div>
    <div class="tool"><svg width="18" height="18" viewBox="0 0 18 18" fill="none" stroke="#111" stroke-width="1.4"><circle cx="9" cy="6" r="4"/><path d="M2 17c0-4 3-6 7-6s7 2 7 6z"/></svg></div>
    <div class="tool"><svg width="18" height="16" viewBox="0 0 18 16" fill="none" stroke="#111" stroke-width="1.4"><path d="M9 15S1 10 1 5a4 4 0 018-1 4 4 0 018 1c0 5-8 10-8 10z"/></svg></div>
    <div class="tool"><svg width="18" height="16" viewBox="0 0 18 16" fill="none" stroke="#111" stroke-width="1.4"><path d="M1 1h3l2 9h9l2-7H5"/><circle cx="7" cy="14" r="1.2"/><circle cx="14" cy="14" r="1.2"/></svg></div>
  </div>
</header>

<nav class="main-nav abs">
  <a>Home</a><a>Products ⌵</a><a>About Us</a><a>News</a><a>FAQ</a><a>Contact</a><a>Personalize your Hammock</a>
</nav>

<section class="hero abs" role="img" aria-label="Person relaxing in a rope hammock on a tropical beach"></section>
<div class="hero-panel abs">
  <h1>Impeccable Design, Superme Finishing,<br>Excellent Comfort &amp; Ease of Maintenance</h1>
  <div class="btn hero-btn abs">Read More</div>
  <svg class="arrow abs" style="left:24px" width="16" height="26" viewBox="0 0 16 26" fill="none" stroke="#111" stroke-width="3"><path d="M13 3L3 13l10 10"/></svg>
  <svg class="arrow abs" style="left:652px" width="16" height="26" viewBox="0 0 16 26" fill="none" stroke="#111" stroke-width="3"><path d="M3 3l10 10L3 23"/></svg>
</div>

<section class="products abs">
  <h2 class="section-title abs" style="top:45px">Our Products</h2>
  <div class="product-card abs" style="left:182px;top:120px;width:407px;height:297px;background:linear-gradient(180deg,#4d6b3a,#6b8a45 50%,#3f5a2c)" role="img" aria-label="Striped hammock on a wooden stand in a garden">
    <div class="name">Product Title</div><div class="cta">Shop Now</div>
  </div>
  <div class="product-card abs" style="left:610px;top:118px;width:407px;height:296px;background:linear-gradient(180deg,#3e6a38,#5d8a44 55%,#4f7a3a)" role="img" aria-label="Hanging hammock chair in a park">
    <div class="name">Product Title</div><div class="cta">Shop Now</div>
  </div>
</section>

<h2 class="section-title abs" style="top:1327px;color:var(--navy)">Featured Products</h2>
<div class="featured-img abs" style="left:182px;top:1399px;background:linear-gradient(180deg,#4b7a3a,#3fa6d6 55%,#2f5a2a)" role="img" aria-label="Cushioned hammock lounger with canopy"></div>
<div class="featured-img abs" style="left:395px;top:1399px;background:linear-gradient(180deg,#3e5d2d,#cfc8b0 50%,#3a5a2b)" role="img" aria-label="Rope hammock on a steel stand"></div>
<div class="featured-img abs" style="left:607px;top:1399px;background:linear-gradient(180deg,#7a8c78,#c6605a 55%,#4a7a34)" role="img" aria-label="Red striped hammock on a stand"></div>
<div class="featured-img abs" style="left:820px;top:1399px;background:linear-gradient(180deg,#4f6f3a,#b59a78 50%,#3f6030)" role="img" aria-label="Fabric hammock on a frame stand"></div>
<div class="item abs" style="left:182px;top:1614px"><div class="by">Vivamus porttitor</div><div class="title">Product Title here</div><div class="price">$13.99</div></div>
<div class="item abs" style="left:395px;top:1618px"><div class="by">Vivamus porttitor</div><div class="title">Product Title here</div><div class="price">$14.99</div></div>
<div class="item abs" style="left:607px;top:1614px"><div class="by">Vivamus porttitor</div><div class="title">Product Title here</div><div class="price">$20.99</div></div>
<div class="item abs" style="left:820px;top:1618px"><div class="by">Vivamus porttitor</div><div class="title">Product Title here</div><div class="price">$18.99</div></div>

<section class="newsletter abs">
  <h2 class="section-title abs" style="top:72px;font-size:30px;color:var(--navy)">Subscribe To Our Newsletter</h2>
  <div class="email abs">Email address</div>
  <div class="btn sub-btn abs">Subscribe</div>
</section>

<footer class="site-footer abs">
  <div class="col abs" style="left:193px;top:58px"><h3>Quick Links</h3><a>Home</a><a>About Us</a><a>Products</a><a>FAQ</a></div>
  <div class="col abs" style="left:420px;top:58px"><h3>Resources</h3><a>My Account</a><a>Shop Now</a><a>Cart</a><a>Register</a></div>
  <div class="col abs" style="left:645px;top:58px"><h3>Follow Us</h3><div class="social"><span></span><span></span><span></span><span></span></div></div>
  <div class="divider abs"></div>
  <div class="cards abs"><span></span><span></span><span></span><span></span><span></span></div>
  <div class="copyright abs">© 2018 Company Name &nbsp;All right reserved &nbsp;Term of Use</div>
</footer>
</body>
</html>
```